****Business Card Design for Quarrystone Development. Design based around attached logo/company name

I’m looking for business card design for my company Quarrystone Development Group,LLC. Design should be professional, sharp and minimal. Outside of the attached logos, greyscale colors for remainder of cards. My thoughts are two-sided card with attached logo on one side and my info on the other but open to one-sided as well with right design.
Target Market(s)
Real estate professionals including banks, private investors, property owners, developers, commercial tenants like Brewlantern, Grovika or Tanquist’s.
Industry/Entity Type
Commercial real estate development and investments.
Contact Information for Business Card
Name, title, email, phone #’s, web address and physical address
Font styles to use
Other font styles liked:
- Helvetica, Garamond, etc
Colors
Designer to choose only greyscale colors for use in the design.
Requirements
Must have
- Attached logo first or second options.
Nice to have
- Two sided card with logo on one side. Attached Logo/company name can be laid out any way that flows as long as it’s legible.name
Should not have
- No loud colors. ***Please do not include logo, I have removed the company design with a logo image.

```html
<!DOCTYPE html>
<html lang="en">
<head>
<meta charset="utf-8">
<title>Quarrystone Development Group, LLC — Business Card</title>
<link href="https://fonts.googleapis.com/css2?family=Cinzel:wght@400&family=Tinos&display=swap" rel="stylesheet">
<style>
  :root {
    --backdrop: #2a2a2b;
    --card: #1e1f21;
    --card-edge: #26272a;
    --brand-grey: #6e6f78;
    --text-grey: #7b7c83;
    --rule-grey: #55565d;
    --icon-grey: #9a9ba1;
  }
  * { margin: 0; padding: 0; box-sizing: border-box; }
  html, body {
    width: 1200px; height: 1138px; overflow: hidden;
    background: var(--backdrop);
  }
  .card {
    position: absolute;
    left: 273px;
    width: 620px;
    height: 360px;
    background: linear-gradient(160deg, var(--card-edge), var(--card) 60%);
    border-radius: 14px;
    box-shadow: 0 4px 14px rgba(0,0,0,0.45);
  }
  .card--front { top: 186px; }
  .card--back { top: 606px; }

  .wordmark {
    position: absolute;
    color: var(--brand-grey);
    font-family: "Cinzel", serif;
    line-height: 1;
  }
  .wordmark__name {
    display: block;
    font-size: 32px;
    letter-spacing: 1px;
    padding-bottom: 4px;
    border-bottom: 1px solid var(--rule-grey);
  }
  .wordmark__group {
    display: block;
    font-size: 13.5px;
    letter-spacing: 2.2px;
    margin-top: 5px;
  }
  .card--front .wordmark { left: 45px; top: 120px; }
  .card--back .wordmark { right: 29px; top: 46px; text-align: right; }

  .contact {
    position: absolute;
    right: 29px;
    top: 160px;
    text-align: right;
    color: var(--text-grey);
    font-family: "Tinos", serif;
    font-size: 15px;
  }
  .contact__person {
    font-family: "Cinzel", serif;
    font-size: 21px;
    color: var(--brand-grey);
    line-height: 1;
  }
  .contact__title { margin-top: 6px; }
  .contact__address { margin-top: 20px; line-height: 22px; }
  .contact__list { list-style: none; margin-top: 4px; }
  .contact__list li {
    display: flex; justify-content: flex-end; align-items: center;
    gap: 10px; height: 22px;
  }
  .contact__list svg { width: 13px; height: 13px; fill: var(--icon-grey); }
</style>
</head>
<body>
  <section class="card card--front" aria-label="Card front">
    <div class="wordmark">
      <span class="wordmark__name">QUARRYSTONE</span>
      <span class="wordmark__group">DEVELOPMENT GROUP, LLC</span>
    </div>
  </section>

  <section class="card card--back" aria-label="Card back">
    <div class="wordmark">
      <span class="wordmark__name">QUARRYSTONE</span>
      <span class="wordmark__group">DEVELOPMENT GROUP, LLC</span>
    </div>
    <div class="contact">
      <p class="contact__person">DANIEL REED HARTLEY</p>
      <p class="contact__title">Managing Director</p>
      <p class="contact__address">418 Ledgeview Rd., Millbrook,<br>Harlow County, US 27514</p>
      <ul class="contact__list">
        <li>828-555-0147
          <svg viewBox="0 0 16 16" aria-hidden="true"><path d="M2 5c0-2 3-3 6-3s6 1 6 3v1h-3V5H5v1H2z"/><path d="M4 7h8l1 7H3z"/></svg>
        </li>
        <li>daniel@quarrystonedev.com
          <svg viewBox="0 0 16 16" aria-hidden="true"><path d="M1 3h14v10H1z M2 4l6 5 6-5" fill="none" stroke="#9a9ba1" stroke-width="1.6"/></svg>
        </li>
        <li>www.quarrystonedev.com
          <svg viewBox="0 0 16 16" aria-hidden="true"><circle cx="8" cy="8" r="7"/><path d="M1 8h14M8 1v14M3 4h10M3 12h10" stroke="#1e1f21" stroke-width="1"/></svg>
        </li>
      </ul>
    </div>
  </section>
</body>
</html>
```